New Look and Feel for 82 year old Vantrek Ltd. presentations

We are seeking new ideas to have powerpoint-layouts for the group headquarters. Vantrek is an industrial company in maritime, hydraulics, heavy machinery and industrial services. Please read our history and watch the video for a quick familiarization. http://www.vantrek-example.fi/eng/main.php

Our customer relationships are based on trust, with Vantrek providing to customers, cooperation partners and other interest groups products and solutions that produce sustainable benefits.

Vantrek strives to ensure that the environmental impact of the products is considered over the entire life cycle and the processes used by the Group are as environmentally benign as possible.

Industry/Entity Type

It Company

Colors

Designer to choose colors to be used in the design.

Requirements
Must have
• Logo
Nice to have
• example animations and transitions

```html
<!DOCTYPE html>
<html lang="en">
<head>
<meta charset="utf-8">
<title>Vantrek presentation layouts</title>
<link href="https://fonts.googleapis.com/css2?family=Montserrat:wght@500;600;700&family=Open+Sans:wght@400;600&display=swap" rel="stylesheet">
<style>
:root{
  --red:#e8383f;
  --dark:#2f2f33;
  --gray:#6e6d6d;
  --mid:#8f8f8f;
  --light:#d9d9d9;
  --pale:#eeeeee;
  --ink:#333;
  --muted:#aaa;
  --white:#fff;
}
*{box-sizing:border-box;margin:0;padding:0}
html,body{width:959px;height:1200px;overflow:hidden;background:#fff}
body{font-family:"Open Sans",Arial,sans-serif;color:var(--ink)}
.board{display:grid;grid-template-columns:repeat(3,313px);grid-auto-rows:235px;gap:6px;padding:0 4px}
.slide{position:relative;background:var(--white);overflow:hidden;box-shadow:0 1px 3px rgba(0,0,0,.25)}
.slide-title{position:absolute;left:17px;top:12px;font-family:"Montserrat",sans-serif;font-weight:600;font-size:14px;color:var(--ink)}
.slide-title::after{content:"";display:block;width:26px;height:2px;background:var(--red);margin-top:4px}
.brand{position:absolute;right:10px;top:13px;display:flex;align-items:center;gap:3px;font-family:"Montserrat",sans-serif;font-weight:700;font-size:8px;color:var(--dark)}
.brand i{width:7px;height:7px;background:var(--red)}
.footer{position:absolute;left:0;right:0;bottom:6px;height:9px;border-top:3px solid var(--dark);border-bottom:3px solid var(--dark);background:var(--red);background-clip:padding-box}
.footer::before,.footer::after{content:"";position:absolute;left:0;right:0;height:1px;background:#fff}
.footer::before{top:0}.footer::after{bottom:0}
.copy{position:absolute;right:12px;bottom:18px;font-size:3px;color:var(--muted)}
.tiny{font-size:3.6px;line-height:1.35;color:var(--muted)}
.photo{position:absolute}
.ico{position:absolute;border-radius:50%;display:flex;align-items:center;justify-content:center;color:#fff}
.ico svg{width:48%;height:48%}
.glyph{fill:none;stroke:currentColor;stroke-width:2;stroke-linecap:round;stroke-linejoin:round}
/* Three bullets */
.bullets .photo{left:4px;top:45px;width:306px;height:92px;background:linear-gradient(120deg,#3c4460,#5a6a96 45%,#2c3040)}
.bullets .ico{width:36px;height:36px;top:128px}
.bullets .txt{position:absolute;top:168px;width:72px;text-align:center}
/* Four column */
.col-box{position:absolute;top:88px;width:54px;height:78px;border:1px solid var(--light);padding:20px 4px 0}
.col-box b{display:block;font-size:3.6px;text-align:center;color:var(--dark);line-height:1.3}
.col-box.hot b{color:var(--red)}
.col-box .ico{width:22px;height:22px;top:-12px;left:15px}
/* Circle infographic */
.ring{position:absolute;left:94px;top:64px;width:124px;height:124px;border-radius:50%;
  background:conic-gradient(var(--red) 0 45deg,var(--mid) 45deg 90deg,var(--dark) 90deg 135deg,var(--red) 135deg 180deg,var(--mid) 180deg 225deg,var(--dark) 225deg 270deg,var(--mid) 270deg 315deg,var(--dark) 315deg 360deg);
  -webkit-mask:radial-gradient(circle,transparent 52%,#000 53%);mask:radial-gradient(circle,transparent 52%,#000 53%)}
.ring-icon{position:absolute;width:12px;height:12px;color:#fff}
.ring-core{position:absolute;left:130px;top:116px;width:52px;text-align:center;font-family:"Montserrat",sans-serif;font-weight:700;font-size:9px;color:var(--dark)}
.side{position:absolute;width:60px}
.side h4{font-size:4px;font-weight:600;color:var(--dark)}
.side.hot h4{color:var(--red)}
.circle-infographic .ico{width:20px;height:20px}
/* Section breaks */
.section{color:#fff;text-align:center}
.section .band{position:absolute;left:0;right:0;top:114px;height:22px}
.section .mark{position:absolute;left:50%;transform:translateX(-50%);top:110px;padding:0 8px;font-family:"Montserrat",sans-serif;font-weight:700;font-size:12px;line-height:30px}
.section h2{position:absolute;left:0;right:0;top:143px;font-family:"Montserrat",sans-serif;font-weight:700;font-size:15px}
.section p{position:absolute;left:60px;right:60px;top:163px;font-size:5px;line-height:1.25}
.sec-dark{background:var(--dark)} .sec-dark .band{background:var(--red)} .sec-dark .mark{background:var(--dark)}
.sec-red{background:var(--red)} .sec-red .band{background:var(--dark)} .sec-red .mark{background:var(--red)}
.sec-gray{background:var(--gray)}
.sec-gray .vband{position:absolute;left:74px;width:54px;background:var(--red)}
.sec-gray .mark{left:100px;background:var(--gray)}
/* Map */
.map{left:66px;top:58px;width:210px;height:116px;background:linear-gradient(160deg,#e2e2e2,#d2d2d2)}
.pin{position:absolute;width:10px;height:12px;color:var(--dark)}
.pin svg{width:100%;height:100%;fill:currentColor}
/* Portfolio */
.cell{position:absolute;width:86px;height:52px;padding:6px;color:#fff}
.cell h5{font-size:5px;font-weight:400;margin-bottom:3px}
.cell .tiny{color:rgba(255,255,255,.8)}
/* Team */
.avatar{left:38px;top:70px;width:74px;height:74px;border-radius:50%;background:radial-gradient(circle at 50% 40%,#c9b9a8,#7f8c99)}
/* Mockup */
.monitor{position:absolute;left:19px;top:68px;width:126px;height:82px;background:var(--dark);border:3px solid #444;border-radius:3px}
.monitor .screen{position:absolute;inset:6px;background:#1d1d1f;display:flex;align-items:center;justify-content:center;gap:4px;font-family:"Montserrat",sans-serif;font-weight:700;font-size:14px;color:#fff}
.monitor .screen i{width:12px;height:12px;background:var(--red)}
.stand{position:absolute;left:70px;top:150px;width:24px;height:12px;background:linear-gradient(#ccc,#eee)}
.foot{position:absolute;left:56px;top:162px;width:52px;height:3px;background:#bbb;border-radius:2px}
.feature{position:absolute;left:180px;width:120px;display:flex;gap:6px}
.feature .ico{position:static;flex:none;width:17px;height:17px}
.feature h6{font-size:5.5px;font-weight:400;color:var(--dark)}
.feature.hot h6{color:var(--red)}
/* Donuts */
.stat{position:absolute;top:64px;width:60px;text-align:center}
.stat strong{display:block;font-family:"Montserrat",sans-serif;font-weight:600;font-size:9px;color:var(--dark);margin-top:4px}
.stat.hot strong{color:var(--red)}
.stat .lbl{font-size:3.8px;color:var(--muted);margin:3px 0}
/* Price */
.plan{position:absolute;top:62px;width:55px;height:130px;border:1px solid var(--light);text-align:center}
.plan .hd{height:11px;line-height:11px;font-size:4.5px;color:#fff;background:var(--mid)}
.plan .price{font-family:"Montserrat",sans-serif;font-size:10px;margin-top:6px;color:var(--dark)}
.plan .pm{font-size:3px;color:var(--muted);margin-bottom:5px}
.plan .ft{position:absolute;left:0;right:0;bottom:0;height:6px;font-size:3px;line-height:6px;color:#fff;background:var(--mid)}
/* Pricing table */
.tier{position:absolute;top:86px;width:44px;text-align:center}
.tier .nm{font-size:4px;color:var(--dark)}
.tier .circ{width:18px;height:18px;border:1.5px solid var(--dark);border-radius:50%;margin:3px auto;display:flex;align-items:center;justify-content:center;color:var(--dark)}
.tier .circ svg{width:10px;height:10px}
.tier .amt{font-family:"Montserrat",sans-serif;font-weight:600;font-size:12px;color:var(--dark);border-bottom:1px dashed var(--muted);line-height:1.1;padding-bottom:1px}
.tier .amt small{display:block;font-size:4px}
.tier .tiny{margin-top:3px}
.tier.hot .nm,.tier.hot .amt,.tier.hot .circ{color:var(--red)} .tier.hot .circ{border-color:var(--red)}
.tier.soft .nm,.tier.soft .amt,.tier.soft .circ{color:var(--muted)} .tier.soft .circ{border-color:var(--muted)}
/* Social */
.social .ico{width:28px;height:28px;top:80px}
.bar{position:absolute;bottom:15px;width:20px;background:var(--pale)}
.bar .fill{position:absolute;left:0;right:0;bottom:0;color:#fff;font-size:7px;text-align:center;padding-top:4px}
/* Pie */
.pie{position:absolute;left:40px;top:97px;width:120px;height:72px;border-radius:50%;
  background:conic-gradient(var(--dark) 0 100deg,var(--red) 100deg 160deg,var(--mid) 160deg 230deg,var(--light) 230deg 270deg,#1d1d1f 270deg 360deg);
  box-shadow:0 6px 0 #1d1d1f}
.legend{position:absolute;left:184px;width:110px}
.legend h6{font-size:4px;font-weight:600;color:var(--dark);display:flex;align-items:center;gap:3px}
.legend h6::before{content:"";width:4px;height:4px;border:1px solid var(--dark);border-radius:50%}
.legend .hot::before{border-color:var(--red)}
</style>
</head>
<body>
<svg width="0" height="0" style="position:absolute" aria-hidden="true">
  <defs>
    <symbol id="i-share" viewBox="0 0 24 24"><g class="glyph"><circle cx="18" cy="5" r="3"/><circle cx="6" cy="12" r="3"/><circle cx="18" cy="19" r="3"/><path d="M8.6 10.5l6.8-4M8.6 13.5l6.8 4"/></g></symbol>
    <symbol id="i-layers" viewBox="0 0 24 24"><g class="glyph"><path d="M12 3l9 5-9 5-9-5z"/><path d="M3 12l9 5 9-5M3 16l9 5 9-5"/></g></symbol>
    <symbol id="i-star" viewBox="0 0 24 24"><g class="glyph"><path d="M12 3l2.7 5.6 6.1.9-4.4 4.3 1 6.1L12 17l-5.4 2.9 1-6.1-4.4-4.3 6.1-.9z"/></g></symbol>
    <symbol id="i-trophy" viewBox="0 0 24 24"><g class="glyph"><path d="M7 4h10v5a5 5 0 0 1-10 0z"/><path d="M12 14v4M8 20h8M7 6H4a3 3 0 0 0 3 4M17 6h3a3 3 0 0 1-3 4"/></g></symbol>
    <symbol id="i-crown" viewBox="0 0 24 24"><g class="glyph"><path d="M3 8l4 5 5-7 5 7 4-5-2 10H5z"/></g></symbol>
    <symbol id="i-rocket" viewBox="0 0 24 24"><g class="glyph"><path d="M5 19l1-4 9-9c2-2 4-2 5-2 0 1 0 3-2 5l-9 9z"/><path d="M9 18l-3 3M6 15l-3 3"/><circle cx="15" cy="9" r="1.5"/></g></symbol>
    <symbol id="i-award" viewBox="0 0 24 24"><g class="glyph"><circle cx="12" cy="9" r="5"/><path d="M9 13l-1 8 4-2 4 2-1-8"/></g></symbol>
    <symbol id="i-lock" viewBox="0 0 24 24"><g class="glyph"><rect x="5" y="11" width="14" height="10" rx="1"/><path d="M8 11V7a4 4 0 0 1 8 0v4"/></g></symbol>
    <symbol id="i-bulb" viewBox="0 0 24 24"><g class="glyph"><path d="M9 18h6M10 21h4M12 3a6 6 0 0 0-4 10.5c1 1 1 2 1 2.5h6c0-.5 0-1.5 1-2.5A6 6 0 0 0 12 3z"/></g></symbol>
    <symbol id="i-target" viewBox="0 0 24 24"><g class="glyph"><circle cx="12" cy="12" r="8"/><circle cx="12" cy="12" r="3"/></g></symbol>
    <symbol id="i-doc" viewBox="0 0 24 24"><g class="glyph"><rect x="5" y="3" width="14" height="18" rx="1"/><path d="M8 8h8M8 12h8M8 16h5"/></g></symbol>
    <symbol id="i-monitor" viewBox="0 0 24 24"><g class="glyph"><rect x="3" y="4" width="18" height="12" rx="1"/><path d="M8 20h8M12 16v4"/></g></symbol>
    <symbol id="i-pencil" viewBox="0 0 24 24"><g class="glyph"><path d="M4 20l1-4L16 5l3 3L8 19z"/></g></symbol>
    <symbol id="i-cart" viewBox="0 0 24 24"><g class="glyph"><circle cx="9" cy="20" r="1.5"/><circle cx="17" cy="20" r="1.5"/><path d="M3 4h3l2 11h11l2-8H7"/></g></symbol>
    <symbol id="i-home" viewBox="0 0 24 24"><g class="glyph"><path d="M3 11l9-7 9 7M5 10v10h14V10"/></g></symbol>
    <symbol id="i-cloud" viewBox="0 0 24 24"><g class="glyph"><path d="M7 18h10a4 4 0 0 0 0-8 6 6 0 0 0-11 1 3.5 3.5 0 0 0 1 7z"/></g></symbol>
    <symbol id="i-heart" viewBox="0 0 24 24"><g class="glyph"><path d="M12 20s-8-5-8-11a4 4 0 0 1 8-1 4 4 0 0 1 8 1c0 6-8 11-8 11z"/></g></symbol>
    <symbol id="i-cap" viewBox="0 0 24 24"><g class="glyph"><path d="M12 5l10 5-10 5L2 10z"/><path d="M6 12v5c3 2 9 2 12 0v-5"/></g></symbol>
    <symbol id="i-globe" viewBox="0 0 24 24"><g class="glyph"><circle cx="12" cy="12" r="9"/><ellipse cx="12" cy="12" rx="4" ry="9"/><path d="M3 12h18"/></g></symbol>
    <symbol id="i-gear" viewBox="0 0 24 24"><g class="glyph"><circle cx="12" cy="12" r="3"/><path d="M12 2v3M12 19v3M2 12h3M19 12h3M5 5l2 2M17 17l2 2M5 19l2-2M17 7l2-2"/></g></symbol>
    <symbol id="i-send" viewBox="0 0 24 24"><g class="glyph"><path d="M21 3L3 11l7 3 3 7z"/><path d="M10 14l11-11"/></g></symbol>
    <symbol id="i-pin" viewBox="0 0 24 24"><path d="M12 22s7-7 7-12a7 7 0 0 0-14 0c0 5 7 12 7 12zm0-9.5a2.5 2.5 0 1 1 0-5 2.5 2.5 0 0 1 0 5z"/></symbol>
  </defs>
</svg>
<main class="board">

<section class="slide bullets">
  <h1 class="slide-title">Three Bullets Area</h1><div class="brand"><i></i>Vantrek</div>
  <div class="photo" role="img" aria-label="Photo of heavy machinery in an industrial workshop"></div>
  <div class="ico" style="left:40px;background:var(--dark)"><svg><use href="#i-share"/></svg></div>
  <div class="ico" style="left:140px;background:var(--red)"><svg><use href="#i-layers"/></svg></div>
  <div class="ico" style="left:240px;background:var(--gray)"><svg><use href="#i-star"/></svg></div>
  <p class="txt tiny" style="left:22px">Steel parts made to order, sized and checked for heavy duty.</p>
  <p class="txt tiny" style="left:122px">Steel parts made to order, sized and checked for heavy duty.</p>
  <p class="txt tiny" style="left:222px">Steel parts made to order, sized and checked for heavy duty.</p>
  <div class="footer"></div><p class="copy">© Vantrek. All rights reserved.</p>
</section>

<section class="slide four-col">
  <h1 class="slide-title">Four Column Area</h1><div class="brand"><i></i>Vantrek</div>
  <div class="col-box" style="left:22px"><div class="ico" style="background:var(--dark)"><svg><use href="#i-trophy"/></svg></div><b>EXPLORATION OF THE FIELD AREA</b><p class="tiny">• Solid steel work<br>• Joint service<br>• Sound design</p></div>
  <div class="col-box hot" style="left:94px"><div class="ico" style="background:var(--red)"><svg><use href="#i-crown"/></svg></div><b>EXPLORATION OF THE FIELD AREA</b><p class="tiny">• Solid steel work<br>• Joint service<br>• Sound design</p></div>
  <div class="col-box" style="left:166px"><div class="ico" style="background:var(--gray)"><svg><use href="#i-rocket"/></svg></div><b>EXPLORATION OF THE FIELD AREA</b><p class="tiny">• Solid steel work<br>• Joint service<br>• Sound design</p></div>
  <div class="col-box" style="left:238px"><div class="ico" style="background:var(--light)"><svg><use href="#i-award"/></svg></div><b style="color:var(--muted)">EXPLORATION OF THE FIELD AREA</b><p class="tiny">• Solid steel work<br>• Joint service<br>• Sound design</p></div>
  <div class="footer"></div><p class="copy">© Vantrek. All rights reserved.</p>
</section>

<section class="slide circle-infographic">
  <h1 class="slide-title">Circle Infographic</h1><div class="brand"><i></i>Vantrek</div>
  <div class="ring"></div>
  <svg class="ring-icon" style="left:170px;top:77px"><use href="#i-globe"/></svg>
  <svg class="ring-icon" style="left:193px;top:100px"><use href="#i-bulb"/></svg>
  <svg class="ring-icon" style="left:193px;top:134px"><use href="#i-gear"/></svg>
  <svg class="ring-icon" style="left:170px;top:157px"><use href="#i-send"/></svg>
  <svg class="ring-icon" style="left:130px;top:157px"><use href="#i-home"/></svg>
  <svg class="ring-icon" style="left:107px;top:134px"><use href="#i-target"/></svg>
  <svg class="ring-icon" style="left:107px;top:100px"><use href="#i-share"/></svg>
  <svg class="ring-icon" style="left:130px;top:77px"><use href="#i-doc"/></svg>
  <div class="ring-core">Vantrek</div>
  <div class="side" style="left:8px;top:88px;text-align:right"><h4>Secure</h4><p class="tiny">Safe parts for sea and land use.</p></div>
  <div class="ico" style="left:70px;top:92px;background:var(--dark)"><svg><use href="#i-lock"/></svg></div>
  <div class="side" style="left:8px;top:147px;text-align:right"><h4>Good Package</h4><p class="tiny">Safe parts for sea and land use.</p></div>
  <div class="ico" style="left:70px;top:150px;background:var(--gray)"><svg><use href="#i-bulb"/></svg></div>
  <div class="ico" style="left:224px;top:92px;background:var(--red)"><svg><use href="#i-gear"/></svg></div>
  <div class="side hot" style="left:248px;top:88px"><h4>Well Organized</h4><p class="tiny">Safe parts for sea and land use.</p></div>
  <div class="ico" style="left:224px;top:150px;background:var(--light)"><svg><use href="#i-doc"/></svg></div>
  <div class="side" style="left:248px;top:147px"><h4>Publication</h4><p class="tiny">Safe parts for sea and land use.</p></div>
  <div class="footer"></div><p class="copy">© Vantrek. All rights reserved.</p>
</section>

<section class="slide section sec-dark">
  <div class="band"></div><div class="mark">Vantrek</div>
  <h2>Section Break</h2>
  <p>Heavy machinery, hydraulics and marine service built on trust and lasting value for every client.</p>
</section>

<section class="slide section sec-red">
  <div class="band"></div><div class="mark">Vantrek</div>
  <h2>Section Break</h2>
  <p>Heavy machinery, hydraulics and marine service built on trust and lasting value for every client.</p>
</section>

<section class="slide section sec-gray">
  <div class="vband" style="top:0;height:100px"></div><div class="vband" style="top:188px;height:47px"></div>
  <div class="mark">Vantrek</div>
  <h2>Section Break</h2>
  <p>Heavy machinery, hydraulics and marine service built on trust and lasting value for every client.</p>
</section>

<section class="slide">
  <h1 class="slide-title">Global Experience</h1><div class="brand"><i></i>Vantrek</div>
  <div class="photo map" role="img" aria-label="World map in light grey showing office locations"></div>
  <span class="pin" style="left:88px;top:76px"><svg><use href="#i-pin"/></svg></span>
  <span class="pin" style="left:168px;top:67px"><svg><use href="#i-pin"/></svg></span>
  <span class="pin" style="left:191px;top:80px"><svg><use href="#i-pin"/></svg></span>
  <span class="pin" style="left:172px;top:110px"><svg><use href="#i-pin"/></svg></span>
  <span class="pin" style="left:20px;top:182px"><svg><use href="#i-pin"/></svg></span>
  <p style="position:absolute;left:38px;top:183px;font-size:6px;color:var(--gray)">Heading Goes Here</p>
  <p class="tiny" style="position:absolute;left:20px;top:195px;width:230px">Sites across the sea lanes serve ships, yards and plants with parts and skilled crews.</p>
  <div class="footer"></div><p class="copy">© Vantrek. All rights reserved.</p>
</section>

<section class="slide">
  <h1 class="slide-title">Portfolio Area</h1><div class="brand"><i></i>Vantrek</div>
  <div class="cell photo" style="left:22px;top:64px;background:linear-gradient(135deg,#3b4a5c,#9aa7b5)" role="img" aria-label="Photo of a control screen"></div>
  <div class="cell" style="left:112px;top:64px;background:var(--red)"><h5>Heading Goes Here</h5><p class="tiny">Work done for a port client on lift gear and deck drives.</p></div>
  <div class="cell photo" style="left:202px;top:64px;background:linear-gradient(135deg,#2e3b56,#8d7f70)" role="img" aria-label="Photo of a technician servicing machinery"></div>
  <div class="cell" style="left:22px;top:120px;background:var(--dark)"><h5>Heading Goes Here</h5><p class="tiny">Work done for a port client on lift gear and deck drives.</p></div>
  <div class="cell photo" style="left:112px;top:120px;background:linear-gradient(135deg,#3a3f4b,#a66a3a)" role="img" aria-label="Photo of a worker at a machine"></div>
  <div class="cell" style="left:202px;top:120px;background:var(--gray)"><h5>Heading Goes Here</h5><p class="tiny">Work done for a port client on lift gear and deck drives.</p></div>
  <div class="footer"></div><p class="copy">© Vantrek. All rights reserved.</p>
</section>

<section class="slide">
  <h1 class="slide-title">Our Team</h1><div class="brand"><i></i>Vantrek</div>
  <div class="photo avatar" role="img" aria-label="Portrait photo of the chief executive"></div>
  <p style="position:absolute;left:50px;top:150px;width:50px;text-align:center;font-size:4px;color:var(--dark)">Mr Aaron Reede<br><span style="color:var(--red)">CEO</span></p>
  <p class="tiny" style="position:absolute;left:124px;top:92px;width:160px">He leads the group with care for staff, clients and the long life of every product we build.<br><br>Thirty years in yards and plants shaped a calm and practical way of working.</p>
  <div style="position:absolute;left:124px;top:125px;display:flex;gap:2px"><i style="width:5px;height:5px;border-radius:50%;background:var(--dark)"></i><i style="width:5px;height:5px;border-radius:50%;background:var(--dark)"></i><i style="width:5px;height:5px;border-radius:50%;background:var(--dark)"></i><i style="width:5px;height:5px;border-radius:50%;background:var(--dark)"></i></div>
  <div class="footer"></div><p class="copy">© Vantrek. All rights reserved.</p>
</section>

<section class="slide">
  <h1 class="slide-title">Product Mockup</h1><div class="brand"><i></i>Vantrek</div>
  <div class="monitor"><div class="screen"><i></i>Vantrek</div></div><div class="stand"></div><div class="foot"></div>
  <div class="feature" style="top:70px"><span class="ico" style="background:var(--dark)"><svg><use href="#i-monitor"/></svg></span><div><h6>Content Title</h6><p class="tiny">Short note on this part of the offer.</p></div></div>
  <div class="feature hot" style="top:96px"><span class="ico" style="background:var(--red)"><svg><use href="#i-pencil"/></svg></span><div><h6>Content Title</h6><p class="tiny">Short note on this part of the offer.</p></div></div>
  <div class="feature" style="top:124px"><span class="ico" style="background:var(--gray)"><svg><use href="#i-cart"/></svg></span><div><h6>Content Title</h6><p class="tiny">Short note on this part of the offer.</p></div></div>
  <div class="feature" style="top:152px"><span class="ico" style="background:var(--light)"><svg><use href="#i-home"/></svg></span><div><h6 style="color:var(--muted)">Content Title</h6><p class="tiny">Short note on this part of the offer.</p></div></div>
  <div class="footer"></div><p class="copy">© Vantrek. All rights reserved.</p>
</section>

<section class="slide">
  <h1 class="slide-title">Chart Title</h1><div class="brand"><i></i>Vantrek</div>
  <div class="stat" style="left:26px"><svg width="46" height="46" viewBox="0 0 46 46"><circle cx="23" cy="23" r="19" fill="none" stroke="var(--pale)" stroke-width="3"/><circle cx="23" cy="23" r="19" fill="none" stroke="var(--dark)" stroke-width="3" stroke-dasharray="71.6 120" transform="rotate(-90 23 23)"/><circle cx="23" cy="23" r="12" fill="var(--gray)"/><text x="23" y="26" font-size="7" fill="#fff" text-anchor="middle">60%</text></svg><strong>89,750</strong><p class="lbl">Growing Company</p><p class="tiny">Plain words on the year and how the group grew in steady steps.</p></div>
  <div class="stat hot" style="left:93px"><svg width="46" height="46" viewBox="0 0 46 46"><circle cx="23" cy="23" r="19" fill="none" stroke="var(--pale)" stroke-width="3"/><circle cx="23" cy="23" r="19" fill="none" stroke="var(--red)" stroke-width="3" stroke-dasharray="29.8 120" transform="rotate(-90 23 23)"/><circle cx="23" cy="23" r="12" fill="var(--red)"/><text x="23" y="26" font-size="7" fill="#fff" text-anchor="middle">25%</text></svg><strong>120,890</strong><p class="lbl">Success Client</p><p class="tiny">Plain words on the year and how the group grew in steady steps.</p></div>
  <div class="stat" style="left:160px"><svg width="46" height="46" viewBox="0 0 46 46"><circle cx="23" cy="23" r="19" fill="none" stroke="var(--pale)" stroke-width="3"/><circle cx="23" cy="23" r="19" fill="none" stroke="var(--gray)" stroke-width="3" stroke-dasharray="53.7 120" transform="rotate(-90 23 23)"/><circle cx="23" cy="23" r="12" fill="var(--mid)"/><text x="23" y="26" font-size="7" fill="#fff" text-anchor="middle">45%</text></svg><strong>2,508</strong><p class="lbl">Subscribers</p><p class="tiny">Plain words on the year and how the group grew in steady steps.</p></div>
  <div class="stat" style="left:227px"><svg width="46" height="46" viewBox="0 0 46 46"><circle cx="23" cy="23" r="19" fill="none" stroke="var(--pale)" stroke-width="3"/><circle cx="23" cy="23" r="19" fill="none" stroke="var(--mid)" stroke-width="3" stroke-dasharray="17.9 120" transform="rotate(-90 23 23)"/><circle cx="23" cy="23" r="12" fill="var(--light)"/><text x="23" y="26" font-size="7" fill="#fff" text-anchor="middle">15%</text></svg><strong style="color:var(--muted)">75,600</strong><p class="lbl">Happy Business</p><p class="tiny">Plain words on the year and how the group grew in steady steps.</p></div>
  <div class="footer"></div><p class="copy">© Vantrek. All rights reserved.</p>
</section>

<section class="slide">
  <h1 class="slide-title">Price Slide</h1><div class="brand"><i></i>Vantrek</div>
  <div class="plan" style="left:12px"><div class="hd">Plan Bronze</div><p class="price">$199</p><p class="pm">Per Month</p><p class="tiny">Basic care plan with yearly checks and parts at list rate.</p><div class="ft">Learn More</div></div>
  <div class="plan" style="left:71px"><div class="hd">Plan Silver</div><p class="price">$299</p><p class="pm">Per Month</p><p class="tiny">Basic care plan with yearly checks and parts at list rate.</p><div class="ft">Learn More</div></div>
  <div class="plan" style="left:130px"><div class="hd" style="background:var(--gray)">Plan Gold</div><p class="price">$399</p><p class="pm">Per Month</p><p class="tiny">Basic care plan with yearly checks and parts at list rate.</p><div class="ft" style="background:var(--gray)">Learn More</div></div>
  <div class="plan" style="left:189px"><div class="hd" style="background:var(--red)">Plan Platinum</div><p class="price">$499</p><p class="pm">Per Month</p><p class="tiny">Basic care plan with yearly checks and parts at list rate.</p><div class="ft" style="background:var(--red)">Learn More</div></div>
  <div class="plan" style="left:248px"><div class="hd" style="background:var(--dark)">Plan Diamond</div><p class="price">$599</p><p class="pm">Per Month</p><p class="tiny">Basic care plan with yearly checks and parts at list rate.</p><div class="ft" style="background:var(--dark)">Learn More</div></div>
  <div class="footer"></div><p class="copy">© Vantrek. All rights reserved.</p>
</section>

<section class="slide">
  <h1 class="slide-title">Pricing Table Plan</h1><div class="brand"><i></i>Vantrek</div>
  <div class="tier" style="left:36px"><p class="nm">Basic</p><div class="circ"><svg><use href="#i-cloud"/></svg></div><p class="amt">$10<small>/ month</small></p><p class="tiny">One site<br>Mail help<br>Yearly check</p></div>
  <div class="tier soft" style="left:86px"><p class="nm">Pro</p><div class="circ"><svg><use href="#i-heart"/></svg></div><p class="amt">$20<small>/ month</small></p><p class="tiny">One site<br>Mail help<br>Yearly check</p></div>
  <div class="tier" style="left:136px"><p class="nm">Advanced</p><div class="circ"><svg><use href="#i-star"/></svg></div><p class="amt">$30<small>/ month</small></p><p class="tiny">One site<br>Mail help<br>Yearly check</p></div>
  <div class="tier hot" style="left:186px"><p class="nm">Business</p><div class="circ"><svg><use href="#i-cap"/></svg></div><p class="amt">$40<small>/ month</small></p><p class="tiny">One site<br>Mail help<br>Yearly check</p></div>
  <div class="tier" style="left:236px"><p class="nm">Platinum</p><div class="circ"><svg><use href="#i-globe"/></svg></div><p class="amt">$50<small>/ month</small></p><p class="tiny">One site<br>Mail help<br>Yearly check</p></div>
  <div class="footer"></div><p class="copy">© Vantrek. All rights reserved.</p>
</section>

<section class="slide social">
  <h1 class="slide-title">Social Media Marketing</h1><div class="brand"><i></i>Vantrek</div>
  <div class="ico" style="left:65px;background:var(--dark)" aria-label="Channel one"></div>
  <div class="ico" style="left:115px;background:var(--red)" aria-label="Channel two"></div>
  <div class="ico" style="left:165px;background:var(--gray)" aria-label="Channel three"></div>
  <div class="ico" style="left:215px;background:var(--mid)" aria-label="Channel four"></div>
  <div class="bar" style="left:69px;height:120px"><div class="fill" style="height:106px;background:var(--dark)">88</div></div>
  <div class="bar" style="left:119px;height:120px"><div class="fill" style="height:65px;background:var(--red)">54</div></div>
  <div class="bar" style="left:169px;height:120px"><div class="fill" style="height:91px;background:var(--gray)">76</div></div>
  <div class="bar" style="left:219px;height:120px"><div class="fill" style="height:44px;background:var(--mid)">37</div></div>
  <div class="footer"></div>
</section>

<section class="slide">
  <h1 class="slide-title">3d Pie Chart</h1><div class="brand"><i></i>Vantrek</div>
  <p style="position:absolute;left:70px;top:76px;font-size:7px;color:var(--gray)">Sales Report</p>
  <div class="pie"></div>
  <p style="position:absolute;left:38px;top:187px;font-size:3.5px;color:var(--muted)">■ Sales A &nbsp; <span style="color:var(--red)">■</span> Sales B &nbsp; ■ Sales C &nbsp; ■ Sales D &nbsp; ■ Sales E</p>
  <div class="legend" style="top:92px"><h6>Black Category</h6><p class="tiny">Short line about this group.</p></div>
  <div class="legend" style="top:105px"><h6 class="hot">Red Category</h6><p class="tiny">Short line about this group.</p></div>
  <div class="legend" style="top:118px"><h6>Gray Category</h6><p class="tiny">Short line about this group.</p></div>
  <div class="legend" style="top:131px"><h6>Light Gray Category</h6><p class="tiny">Short line about this group.</p></div>
  <div class="legend" style="top:144px"><h6>Black Category</h6><p class="tiny">Short line about this group.</p></div>
  <div class="footer"></div><p class="copy">© Vantrek. All rights reserved.</p>
</section>

</main>
</body>
</html>
```